Business Cards for new orthopaedic surgery practice

My husband and I are starting our own orthopaedic surgery practice. We are looking for a business card that is uniform, but one will have my name/title and the other will have his. You can just create one design with my name on it for now. But when I choose your design as the winning design I will ask that you add another copy with his name/title.

We are looking for classy, simple, elite all in one. We like dark blues/a little gold/yellow. Something that goes with our logo. We want our logo incorporated. Here is all the info you need:
Business name: RV Bone & Vitality Center
Location: 38517 North Willowmere Ave
Maple Ridge, FL 33489
Phone: 954-218-4063
Fax: 954-582-7341
Email: info@myrvbonecare.example

Names: Lydia Vance, M.D.
Board Certified Hand and Upper Extremity Surgeon

Ebo Dansu, M.D.
Board Certified Hip & Knee Replacement/General Orthopaedic Surgeon

Can decide what you want to put on the back. Maybe a slogan:
Steady Hands. Stronger Every Day

I am just going to upload our logo. The only thing is if we select you as the winning design, the location, and phone numbers may change. We will need your help to update that once fully solidified.

Industry/Entity Type

Medical

Contact Information for Business Card

Colors
0054AA
0677BA
7BADD7
CADEEF
E8F1F8
0094D4
00A9DD
6FCCEA
C7EBF8
E9F6FB

Requirements
Must have
• class, appeal,
Should not have
• We want to air on the side of masculine if we are looking at masculine vs. feminine feel. But we still want it classy, sophisticated, and something we will love

```html
<!DOCTYPE html>
<html lang="en">
<head>
<meta charset="utf-8">
<title>RV Bone &amp; Vitality Center – Business Card</title>
<link href="https://fonts.googleapis.com/css2?family=Montserrat:wght@400;500;600&display=swap" rel="stylesheet">
<style>
  :root {
    --backdrop: #dedede;
    --card: #ffffff;
    --navy: #1f3d8c;
    --cyan: #00b4e0;
    --ink: #2b2b2b;
    --grey: #555555;
    --violet: #5a5e9a;
  }
  * { margin: 0; padding: 0; box-sizing: border-box; }
  html, body {
    width: 1200px; height: 1200px; overflow: hidden;
    background: var(--backdrop);
    font-family: "Montserrat", sans-serif;
  }
  .card {
    position: absolute; left: 179px; width: 861px; height: 496px;
    background: var(--card);
    box-shadow: 0 8px 18px rgba(0,0,0,0.18);
  }
  .card--front { top: 84px; }
  .card--back { top: 621px; }

  .brand-name {
    position: absolute; left: 0; right: 0; top: 210px;
    text-align: center; font-size: 40px; font-weight: 600;
    color: var(--navy); letter-spacing: 0.5px;
  }
  .tagline {
    position: absolute; left: 0; right: 0; top: 438px;
    text-align: center; font-size: 30px; font-weight: 500;
    color: var(--cyan);
  }

  .practice {
    position: absolute; left: 36px; top: 32px;
    font-size: 32px; font-weight: 600; color: var(--ink); letter-spacing: 0.6px;
  }
  .practice-rule {
    position: absolute; left: 36px; right: 38px; top: 79px;
    height: 3px; background: var(--cyan);
  }
  .doctor {
    position: absolute; left: 36px; top: 92px;
    font-size: 30px; font-weight: 600; color: var(--ink);
  }
  .specialty {
    position: absolute; right: 38px; top: 88px;
    text-align: right; font-size: 28px; line-height: 31px;
    font-weight: 400; color: var(--violet);
  }
  .contact {
    position: absolute; left: 36px; top: 358px;
    list-style: none;
  }
  .contact li { height: 38px; white-space: nowrap; }
  .contact .label { font-size: 26px; font-weight: 500; color: var(--navy); }
  .contact .value { font-size: 22px; color: var(--grey); letter-spacing: 0.6px; margin-left: 6px; }
  .address {
    position: absolute; right: 38px; top: 407px;
    text-align: right; font-style: normal;
    font-size: 22px; line-height: 31px; color: var(--grey);
  }
</style>
</head>
<body>
  <section class="card card--front">
    <div class="brand-name">RV Bone &amp; Vitality Center</div>
    <p class="tagline">Steady Hands. Stronger Every Day</p>
  </section>

  <section class="card card--back">
    <h1 class="practice">RV Orthopaedic Specialists</h1>
    <div class="practice-rule"></div>
    <h2 class="doctor">Lydia Vance, M.D.</h2>
    <p class="specialty">Board Certified Hand and<br>Upper Extremity Surgeon</p>
    <ul class="contact">
      <li><span class="label">Phone.</span><span class="value">954-218-4063</span></li>
      <li><span class="label">Fax.</span><span class="value">954-582-7341</span></li>
      <li><span class="label">Email.</span><span class="value">info@myrvbonecare.example</span></li>
    </ul>
    <address class="address">38517 North Willowmere Ave<br>Maple Ridge, FL 33489</address>
  </section>
</body>
</html>
```